Advanced Therapeutic Massage Therapist

I need a business card advertising my massage services as an advanced therapeutic massage therapist. I offer advanced therapeutic massage, swedish and deep tissue. I want to create a simple, professional and feminine card. I like bright colours and creativity.

I prefer a bold and experimental approach rather than something status-quo. A card to suggest therapeutic healing through dynamic massage. Motifs, shapes or layout which suggest movement and flow.
Updates

Target Market(s)

Everybody!

Industry/Entity Type

Health And Wellness

Contact Information for Business Card

The card should include:
My name, logo, services offered and my contact details.

Sláine Dunleavy
Massage Therapist

- Swedish - Deep Tissue - Advanced Therapeutic

Phone: (+353) 87 216 4093
Email: regenerate@slainedunleavy-example.com
Website: www.slainedunlevy-example.com

Font styles to use
Serif
Sans Serif
Decorative
Script

Colors

Designer to choose colors to be used in the design.

Requirements
Must have
• An example may contain something like this, yet concise:
• "Sláine Dunleavy
• Massage Therapist
• - Swedish - Deep Tissue - Advanced Therapeutic"
Nice to have
• This sentence is optional:
• Imagery such as a logo or symbol. I have attached a file containing a logo I had produced however the name is incorrect now as it is "Sláine" not "Nelly". It could be edited to change it to Sláine.
• I have sent the file as .psd .jpg. .pdf and .png
• I like when the card conveys energy, movement, pressure points, flow etc.
• I just like the designer to follow their own style and ideas. I like bright colours but must have a lot of a base colour to offset it. I really prefer them to follow their own inspiration. That is my preference.
Should not have
• Pine trees, non-native trees to Britain and Ireland, exotic flowers or animals that are not native to Britain and Ireland.
• I don't like brown as the background colour of the card.
• The cars shouldn't look like a wedding invitation i.e too many floral type designs.

```html
<!DOCTYPE html>
<html lang="en">
<head>
<meta charset="utf-8">
<title>Sláine Dunleavy – Massage Therapist Business Card</title>
<link rel="stylesheet" href="https://fonts.googleapis.com/css2?family=Pinyon+Script&family=PT+Sans:wght@400;700&display=swap">
<style>
  :root {
    --stage: #2a2a2b;
    --card: #0d0d0e;
    --card-edge: #1a1a1b;
    --text: #f2f2f2;
    --text-soft: #cfcfcf;
    --bullet: #d8d5bf;
    --mint-light: #cdeee6;
    --mint: #9fd6cb;
    --gold: #c89a3c;
  }
  * { margin: 0; padding: 0; box-sizing: border-box; }
  html, body {
    width: 1200px;
    height: 900px;
    overflow: hidden;
    background: var(--stage);
  }
  .stage {
    width: 1200px;
    height: 900px;
    display: flex;
    align-items: center;
    justify-content: center;
    gap: 48px;
  }
  .card {
    position: relative;
    width: 520px;
    height: 300px;
    background: var(--card);
    border-radius: 22px;
    box-shadow: 0 0 0 1px var(--card-edge);
    font-family: "PT Sans", Arial, sans-serif;
    color: var(--text);
    overflow: hidden;
  }
  .logo-disc {
    position: absolute;
    border-radius: 50%;
    background: radial-gradient(circle at 50% 45%, var(--mint-light) 0%, var(--mint) 75%, var(--gold) 100%);
  }
  /* Info side */
  .card--info .logo-disc {
    width: 158px;
    height: 158px;
    left: 42px;
    top: 71px;
  }
  .info {
    position: absolute;
    left: 248px;
    right: 36px;
    top: 80px;
  }
  .contact {
    list-style: none;
    font-size: 14px;
    color: var(--text-soft);
  }
  .contact li {
    display: flex;
    align-items: center;
    gap: 8px;
    line-height: 23px;
    white-space: nowrap;
  }
  .contact svg { width: 12px; height: 12px; flex: none; }
  .services {
    list-style: none;
    margin-top: 20px;
    font-size: 15px;
    font-weight: 700;
  }
  .services li {
    display: flex;
    align-items: center;
    gap: 9px;
    line-height: 24px;
    white-space: nowrap;
  }
  .services li::before {
    content: "";
    width: 9px;
    height: 9px;
    border-radius: 50%;
    background: var(--bullet);
  }
  /* Name side */
  .card--name .logo-disc {
    width: 138px;
    height: 138px;
    left: 191px;
    top: 44px;
  }
  .identity {
    position: absolute;
    left: 0;
    right: 0;
    top: 192px;
    text-align: center;
  }
  .identity__name {
    font-family: "Pinyon Script", "Brush Script MT", cursive;
    font-weight: 400;
    font-size: 32px;
    line-height: 1;
    color: var(--text);
  }
  .identity__role {
    font-size: 14px;
    letter-spacing: 1.5px;
    color: var(--text-soft);
    margin-top: 2px;
  }
</style>
</head>
<body>
<main class="stage">
  <section class="card card--info">
    <div class="logo-disc" role="img" aria-label="Circular logo emblem in mint and gold"></div>
    <div class="info">
      <ul class="contact">
        <li>
          <svg viewBox="0 0 24 24" aria-hidden="true"><path fill="#e0a23a" d="M6.6 10.8a15.1 15.1 0 0 0 6.6 6.6l2.2-2.2a1 1 0 0 1 1-.25 11.4 11.4 0 0 0 3.6.57 1 1 0 0 1 1 1V20a1 1 0 0 1-1 1A17 17 0 0 1 3 4a1 1 0 0 1 1-1h3.5a1 1 0 0 1 1 1c0 1.25.2 2.45.57 3.57a1 1 0 0 1-.25 1z"/></svg>
          (+353) 87 216 4093
        </li>
        <li>
          <svg viewBox="0 0 24 24" aria-hidden="true"><rect x="2" y="5" width="20" height="14" rx="2" fill="#d9c9a8"/><path d="M2 7l10 6 10-6" fill="none" stroke="#6b5a3a" stroke-width="2"/></svg>
          slainemassage@example-mail.com
        </li>
      </ul>
      <ul class="services">
        <li>Swedish</li>
        <li>Deep Tissue</li>
        <li>Advanced Therapeutic</li>
      </ul>
    </div>
  </section>

  <section class="card card--name">
    <div class="logo-disc" role="img" aria-label="Circular logo emblem in mint and gold"></div>
    <div class="identity">
      <h1 class="identity__name">Sláine Dunleavy</h1>
      <p class="identity__role">massage therapist</p>
    </div>
  </section>
</main>
</body>
</html>
```